K & R Acre Works. Business card design

We need a business card designed for a new business. We have a bulldozer and tractor service. We clear land and make wildlife food plots. We provide disking, bush hogging, and site prep services.
I have attached an image of a business card that I like and would like my business cards to look similar.

Target Market(s)

anyone needing bulldozer and/or tractor services

Industry/Entity Type

Business

Contact Information for Business Card

K & R Acre Works, Operated by 7-T-Ranch
Wade Colton
601-472-3358
wcr4817@fieldmail-example.com

Font styles to use
Sans Serif

Colors

Designer to choose colors to be used in the design.

Requirements
Must have
• image of tractor and bulldozer
• Land Clearing
• Wildlife food plots
• Bush Hogging
• Disking
• Site prep
Nice to have
• i have included a image of a business card that i like. I would like mine to be similar.

```html
<!DOCTYPE html>
<html lang="en">
<head>
<meta charset="utf-8">
<title>K &amp; R Acre Works — Business Card</title>
<link href="https://fonts.googleapis.com/css2?family=Roboto:wght@400;500;700&family=Roboto+Condensed:wght@500;700&display=swap" rel="stylesheet">
<style>
  :root {
    --bg: #e8e8e4;
    --card: #f3f3f1;
    --olive: #9a993a;
    --brown: #6b3f12;
    --text: #555555;
    --dark: #222222;
    --rule: #6f6f6f;
    --dozer-a: #8a8a6a;
    --dozer-b: #6e6248;
    --tractor-a: #7f8f4a;
    --tractor-b: #a3704a;
  }
  html, body {
    margin: 0;
    width: 1200px;
    height: 960px;
    overflow: hidden;
    background: var(--bg);
  }
  .stage { position: relative; width: 1200px; height: 960px; }
  .card {
    position: absolute;
    left: 300px; top: 309px;
    width: 600px; height: 342px;
    transform: scale(1.8);
    transform-origin: center;
    background: var(--card);
    border-radius: 14px;
    overflow: hidden;
    box-shadow: 0 2px 4px rgba(0,0,0,.18);
    font-family: "Roboto", Arial, sans-serif;
    color: var(--text);
  }
  .swoosh { position: absolute; left: 0; top: 0; }
  .brand {
    position: absolute; left: 355px; top: 30px; width: 212px;
  }
  .brand-name {
    display: flex; align-items: center; gap: 6px;
    font-family: "Roboto Condensed", Arial, sans-serif;
    font-weight: 700; font-size: 17px; line-height: 20px;
    color: var(--brown); letter-spacing: .2px;
  }
  .brand-mark { width: 12px; height: 12px; background: var(--olive); }
  .brand-tagline {
    margin-top: 3px;
    font-family: "Roboto Condensed", Arial, sans-serif;
    font-weight: 700; font-size: 8.6px; color: var(--dark);
    white-space: nowrap;
  }
  .photo { position: absolute; top: 69px; height: 68px; }
  .photo-dozer {
    left: 354px; width: 115px;
    background: linear-gradient(160deg, var(--dozer-a), #b5a83a 50%, var(--dozer-b));
  }
  .photo-tractor {
    left: 475px; width: 92px;
    background: linear-gradient(160deg, var(--tractor-a), var(--tractor-b) 55%, #8b9a55);
  }
  .person { position: absolute; left: 34px; top: 191px; }
  .person-name {
    font-family: "Roboto Condensed", Arial, sans-serif;
    font-weight: 700; font-size: 21px; line-height: 24px; color: var(--olive);
  }
  .person-role {
    font-family: "Roboto Condensed", Arial, sans-serif;
    font-weight: 500; font-size: 15px; line-height: 17px; color: var(--brown);
    letter-spacing: .3px;
  }
  .rule {
    position: absolute; left: 33px; top: 243px; width: 537px; height: 1px;
    background: var(--rule);
  }
  .contacts {
    position: absolute; left: 33px; top: 260px;
    list-style: none; margin: 0; padding: 0;
    font-size: 14px; line-height: 18px;
  }
  .contacts li { display: flex; align-items: center; gap: 6px; }
  .contacts svg { width: 13px; height: 13px; fill: var(--olive); }
  .services {
    position: absolute; right: 30px; top: 260px;
    list-style: none; margin: 0; padding: 0;
    font-size: 14px; line-height: 18px; text-align: right;
  }
  .bullet {
    display: inline-block; width: 5px; height: 5px; border-radius: 50%;
    background: var(--olive); margin: 0 4px 2px 6px; vertical-align: middle;
  }
  .bullet.inline { margin: 0 3px 2px 3px; }
  .gap { display: inline-block; width: 10px; }
</style>
</head>
<body>
<div class="stage">
  <div class="card">
    <svg class="swoosh" width="600" height="342" viewBox="0 0 600 342" aria-hidden="true">
      <path d="M0 0 H345 C240 22 60 55 0 112 Z" fill="var(--olive)"/>
      <path d="M0 120 C60 62 240 26 350 1 C240 34 60 80 0 146 Z" fill="var(--brown)"/>
    </svg>

    <div class="brand">
      <div class="brand-name"><span class="brand-mark"></span>K &amp; R ACRE WORKS</div>
      <div class="brand-tagline">FOR ALL OF YOUR LAND IMPROVEMENT NEEDS</div>
    </div>
    <div class="photo photo-dozer" role="img" aria-label="Photo of a yellow bulldozer clearing land"></div>
    <div class="photo photo-tractor" role="img" aria-label="Photo of an orange tractor with a mower in a field"></div>

    <div class="person">
      <div class="person-name">WADE COLTON</div>
      <div class="person-role">OWNER</div>
    </div>
    <div class="rule"></div>

    <ul class="contacts">
      <li><svg viewBox="0 0 24 24"><path d="M6.6 10.8a15.5 15.5 0 0 0 6.6 6.6l2.2-2.2c.3-.3.7-.4 1-.2 1.1.4 2.3.6 3.6.6.6 0 1 .4 1 1V20c0 .6-.4 1-1 1A17 17 0 0 1 3 4c0-.6.4-1 1-1h3.5c.6 0 1 .4 1 1 0 1.3.2 2.5.6 3.6.1.3 0 .7-.2 1z"/></svg>601-472-3358</li>
      <li><svg viewBox="0 0 24 24"><path d="M2 5h20v14H2z M3 6l9 7 9-7" /><path d="M3 6l9 7 9-7" fill="none" stroke="#f3f3f1" stroke-width="1.6"/></svg>wcr4817@fieldmail-example.com</li>
      <li><svg viewBox="0 0 24 24"><circle cx="12" cy="12" r="10"/><path d="M2 12h20M12 2c3 3 3 17 0 20M12 2c-3 3-3 17 0 20" fill="none" stroke="#f3f3f1" stroke-width="1.5"/></svg>kracreworks-example.com</li>
    </ul>

    <ul class="services">
      <li>Land Clearing<span class="bullet"></span></li>
      <li>Wildlife food plots<span class="bullet"></span></li>
      <li>Bush Hogging<span class="bullet inline"></span>Disking<span class="gap"></span>Site prep<span class="bullet"></span></li>
    </ul>
  </div>
</div>
</body>
</html>
```